New Business Card Design Project LORVANTI-Italy

we are LORVANTI-Italy
our company in the market for 3 years we are luxury cosmetic company and its about time for a facelift :)
i will like to have elegant luxurious and unique business card
that will give the person that get it a unique, luxurious and elegant impression
I'm VERY OPEN FOR NEW IDEAS , even duo i add a few files of things that i see on line and i like them

i add my logo as well
my website is LORVANTI.COM
(if you would like to see the main style that we have)

Target Market(s)

adult that have money :)

Industry/Entity Type

Business

Contact Information for Business Card

Name - Dario Lorvanti
Position - CEO and CO Founder
address - 4817 E Halvern
telephone - 555-384-1926
email - dario@lorvanti.com
fax - 555-384-1926
website - LORVANTI.COM

Colors
000000
959595
fbee3e
ffffff

Requirements
Must have
• big logo in GOLD color
• elegant look
• impressive
Nice to have
• not must but maybe classy pattern background
• not must but maybe emblem
• maybe clear plastic business card
Should not have
• colors
• images

```html
<!DOCTYPE html>
<html lang="en">
<head>
<meta charset="utf-8">
<title>LORVANTI-Italy Business Card</title>
<link rel="stylesheet" href="https://fonts.googleapis.com/css2?family=Crimson+Pro:wght@400;500&display=swap">
<style>
  :root {
    --stage: #2b2b2b;
    --card-black: #050708;
    --card-white: #ffffff;
    --gold: #d2af4a;
    --ink-light: #f4f4f4;
  }
  * { margin: 0; padding: 0; box-sizing: border-box; }
  html, body { width: 1200px; height: 864px; overflow: hidden; }
  body {
    background: var(--stage);
    font-family: "Crimson Pro", Georgia, serif;
    position: relative;
  }
  .card {
    position: absolute;
    top: 292px;
    width: 492px;
    height: 280px;
    overflow: hidden;
  }
  .card--front { left: 99px; background: var(--card-black); }
  .card--back { left: 609px; background: var(--card-black); }

  .brand {
    position: absolute;
    top: 62px;
    width: 266px;
    text-align: center;
  }
  .card--front .brand { left: 113px; }
  .card--back .brand { left: 8px; }
  .brand__mark {
    display: block;
    width: 80px;
    height: 80px;
    margin: 0 auto 16px;
    border: 2px solid var(--gold);
    border-radius: 50%;
  }
  .brand__name {
    color: var(--gold);
    font-weight: 400;
    font-size: 36px;
    letter-spacing: 0.5px;
    line-height: 1;
  }

  .card__panel-white {
    position: absolute;
    left: 0; top: 0;
    width: 266px; height: 280px;
    background: var(--card-white);
  }
  .card__stripe {
    position: absolute;
    left: 266px; top: 0;
    width: 4px; height: 280px;
    background: var(--gold);
  }

  .contact {
    position: absolute;
    left: 303px;
    top: 50px;
    color: var(--ink-light);
    font-size: 15px;
    line-height: 18px;
  }
  .contact__name { color: var(--gold); font-size: 21px; font-weight: 500; line-height: 24px; }
  .contact__role { margin-bottom: 14px; }
  .contact__company { color: var(--gold); font-weight: 500; }
  .contact__address { margin-bottom: 14px; }
  .contact__list { list-style: none; }
  .contact__list li { display: flex; align-items: center; gap: 6px; }
  .contact__list svg { width: 12px; height: 12px; fill: var(--gold); flex: none; }
</style>
</head>
<body>
  <section class="card card--front">
    <div class="brand">
      <span class="brand__mark"></span>
      <div class="brand__name">LORVANTI</div>
    </div>
  </section>

  <section class="card card--back">
    <div class="card__panel-white"></div>
    <div class="card__stripe"></div>
    <div class="brand">
      <span class="brand__mark"></span>
      <div class="brand__name">LORVANTI</div>
    </div>

    <div class="contact">
      <div class="contact__name">Dario Lorvanti</div>
      <div class="contact__role">CEO and CO Founder</div>
      <div class="contact__company">LORVANTI-Italy</div>
      <div class="contact__address">4817 E Halvern</div>
      <ul class="contact__list">
        <li>
          <svg viewBox="0 0 12 12" aria-hidden="true"><path d="M2.5 1 L4.5 1 L5 3.5 L3.8 4.4 C4.5 6 6 7.5 7.6 8.2 L8.5 7 L11 7.5 L11 9.5 C11 10.4 10.3 11 9.5 11 C5 10.7 1.3 7 1 2.5 C1 1.7 1.6 1 2.5 1Z"/></svg>
          555-384-1926
        </li>
        <li>
          <svg viewBox="0 0 12 12" aria-hidden="true"><rect x="3" y="1" width="6" height="3"/><rect x="1" y="4.5" width="10" height="4.5" rx="1"/><rect x="3" y="8" width="6" height="3"/></svg>
          555-384-1926
        </li>
        <li>
          <svg viewBox="0 0 12 12" aria-hidden="true"><path d="M1 3 L11 3 L6 6.8Z"/><path d="M1 4.2 L6 8 L11 4.2 L11 9.5 L1 9.5Z"/></svg>
          dario@lorvanti.com
        </li>
        <li>
          <svg viewBox="0 0 12 12" aria-hidden="true"><path d="M6 1a5 5 0 1 0 0.001 0Z M6 2c0.7 0.8 1.2 2.2 1.3 3.5H4.7C4.8 4.2 5.3 2.8 6 2Z M2.1 5.5c0.2-1.5 1.2-2.8 2.5-3.3C4 3.2 3.7 4.3 3.7 5.5Z M8.3 5.5c0-1.2-0.3-2.3-0.9-3.3 1.3 0.5 2.3 1.8 2.5 3.3Z M2.1 6.5h1.6c0 1.2 0.3 2.3 0.9 3.3-1.3-0.5-2.3-1.8-2.5-3.3Z M4.7 6.5h2.6C7.2 7.8 6.7 9.2 6 10 5.3 9.2 4.8 7.8 4.7 6.5Z M8.3 6.5h1.6c-0.2 1.5-1.2 2.8-2.5 3.3 0.6-1 0.9-2.1 0.9-3.3Z"/></svg>
          LORVANTI.COM
        </li>
      </ul>
    </div>
  </section>
</body>
</html>
```